Business card for event manager / organizer "waiter service"

Draft of a new valuable business card for my company.
Events, personnel service providers, festivals

```html
<!DOCTYPE html>
<html lang="de">
<head>
<meta charset="utf-8">
<title>Lenno's Kellnerservice – Visitenkarte</title>
<link href="https://fonts.googleapis.com/css2?family=Lato:wght@300;400;700;900&display=swap" rel="stylesheet">
<style>
  :root {
    --bg: #ecebe8;
    --card-white: #ffffff;
    --ink: #2b2b2b;
    --ink-soft: #4a4a4a;
    --orange: #f39a2b;
    --night-1: #2a2733;
    --night-2: #5b3f8c;
  }
  * { box-sizing: border-box; margin: 0; padding: 0; }
  html, body {
    width: 1200px; height: 919px; overflow: hidden;
    background: var(--bg);
    font-family: "Lato", sans-serif;
  }
  .canvas {
    position: relative; width: 1200px; height: 919px;
    display: flex; align-items: center; justify-content: center; gap: 40px;
  }
  .card {
    position: relative; width: 540px; height: 350px;
    border-radius: 28px; overflow: hidden;
    box-shadow: 0 10px 30px rgba(0,0,0,.18);
  }

  /* Front */
  .card--front { background: var(--card-white); color: var(--ink); }
  .brand {
    position: absolute; left: 34px; top: 44px; width: 210px;
    text-align: center;
  }
  .brand__row { display: flex; align-items: center; justify-content: center; gap: 8px; }
  .brand__mark { width: 14px; height: 14px; background: var(--orange); border-radius: 50%; flex: none; }
  .brand__name {
    font-weight: 900; font-size: 22px; line-height: 1.05; color: var(--ink);
  }
  .brand__tagline {
    margin-top: 6px; font-weight: 300; font-size: 9.5px; color: var(--ink-soft);
  }
  .portrait {
    position: absolute; left: 74px; top: 150px; width: 132px; height: 132px;
    border-radius: 50%; border: 2px solid var(--orange); padding: 4px;
  }
  .portrait__fill {
    width: 100%; height: 100%; border-radius: 50%;
    background: radial-gradient(circle at 50% 40%, #8a8a8a, #3c3c3c 75%);
  }
  .divider {
    position: absolute; left: 268px; top: 92px; width: 2px; height: 200px;
    background: var(--orange);
  }
  .person { position: absolute; left: 296px; top: 96px; right: 16px; }
  .person__name { font-size: 27px; font-weight: 400; color: var(--ink); white-space: nowrap; }
  .person__role { font-size: 16px; font-weight: 400; color: var(--orange); margin-top: 2px; }
  .contact { list-style: none; margin-top: 16px; }
  .contact__item {
    display: flex; align-items: center; gap: 9px;
    font-size: 14px; line-height: 21px; color: var(--ink-soft); white-space: nowrap;
  }
  .contact__icon { width: 12px; height: 12px; flex: none; fill: var(--orange); }

  /* Back */
  .card--back { background: var(--night-1); }
  .scene {
    position: absolute; inset: 0;
    background:
      radial-gradient(ellipse at 78% 35%, rgba(214,170,90,.75), transparent 45%),
      radial-gradient(ellipse at 40% 10%, rgba(150,110,210,.8), transparent 55%),
      linear-gradient(180deg, var(--night-2) 0%, #3a2e55 45%, var(--night-1) 100%);
  }
  .back-brand {
    position: absolute; inset: 0;
    display: flex; flex-direction: column; align-items: center; justify-content: center;
  }
  .back-brand__row { display: flex; align-items: center; gap: 14px; }
  .back-brand__mark { width: 26px; height: 26px; background: var(--orange); flex: none; }
  .back-brand__name { font-weight: 900; font-size: 40px; color: #ffffff; line-height: 1; white-space: nowrap; }
  .back-brand__tagline { margin-top: 12px; font-weight: 300; font-size: 16px; color: #ffffff; }
</style>
</head>
<body>
<main class="canvas">

  <section class="card card--front" aria-label="Visitenkarte Vorderseite">
    <div class="brand">
      <div class="brand__row">
        <span class="brand__mark"></span>
        <span class="brand__name">Lenno's<br>Kellnerservice</span>
      </div>
      <p class="brand__tagline">…für Gäste, die gern wiederkommen!</p>
    </div>

    <div class="portrait">
      <div class="portrait__fill" role="img" aria-label="Porträtfoto des Inhabers"></div>
    </div>

    <div class="divider"></div>

    <div class="person">
      <h1 class="person__name">Jonas Brettmann</h1>
      <p class="person__role">Inhaber</p>
      <ul class="contact">
        <li class="contact__item">
          <svg class="contact__icon" viewBox="0 0 24 24"><path d="M6.6 10.8a15.1 15.1 0 0 0 6.6 6.6l2.2-2.2a1 1 0 0 1 1-.25 11.4 11.4 0 0 0 3.6.57 1 1 0 0 1 1 1V20a1 1 0 0 1-1 1A17 17 0 0 1 3 4a1 1 0 0 1 1-1h3.5a1 1 0 0 1 1 1c0 1.250.2 2.45.57 3.57a1 1 0 0 1-.25 1z"/></svg>
          02361 507 21 48
        </li>
        <li class="contact__item">
          <svg class="contact__icon" viewBox="0 0 24 24"><path d="M7 1h10a2 2 0 0 1 2 2v18a2 2 0 0 1-2 2H7a2 2 0 0 1-2-2V3a2 2 0 0 1 2-2zm0 3v14h10V4zm5 15.5a1 1 0 1 0 0 2 1 1 0 0 0 0-2z"/></svg>
          0176 482 31 07
        </li>
        <li class="contact__item">
          <svg class="contact__icon" viewBox="0 0 24 24"><path d="M2 11 22 2l-9 20-2-9z"/></svg>
          info@lennos-kellnerservice.de
        </li>
        <li class="contact__item">
          <svg class="contact__icon" viewBox="0 0 24 24"><path d="M12 2a10 10 0 1 0 0 20 10 10 0 0 0 0-20zm0 2c.9 0 2.2 1.8 2.7 5H9.3C9.8 5.8 11.1 4 12 4zM4.3 13h3c.1 1.3.3 2.6.6 3.7A8 8 0 0 1 4.3 13zm0-2a8 8 0 0 1 3.6-3.7c-.3 1.1-.5 2.4-.6 3.7zm7.7 9c-.9 0-2.2-1.8-2.7-5h5.4c-.5 3.2-1.8 5-2.7 5zm4.1-3.3c.3-1.1.5-2.4.6-3.7h3a8 8 0 0 1-3.6 3.7zm.6-5.7c-.1-1.3-.3-2.6-.6-3.7a8 8 0 0 1 3.6 3.7z"/></svg>
          lennos-kellnerservice.de
        </li>
        <li class="contact__item">
          <svg class="contact__icon" viewBox="0 0 24 24"><path d="M12 2a7 7 0 0 0-7 7c0 5 7 13 7 13s7-8 7-13a7 7 0 0 0-7-7zm0 9.5A2.5 2.5 0 1 1 12 6.5a2.5 2.5 0 0 1 0 5z"/></svg>
          Birkenweg 14, 45701 Lindenfeld
        </li>
        <li class="contact__item">
          <svg class="contact__icon" viewBox="0 0 24 24"><circle cx="12" cy="12" r="10"/></svg>
          /lennoskellnerservice
        </li>
      </ul>
    </div>
  </section>

  <section class="card card--back" aria-label="Visitenkarte Rückseite">
    <div class="scene" role="img" aria-label="Konzertfoto mit feiernder Menge vor violetter Bühnenbeleuchtung"></div>
    <div class="back-brand">
      <div class="back-brand__row">
        <span class="back-brand__mark"></span>
        <span class="back-brand__name">Lenno's Kellnerservice</span>
      </div>
      <p class="back-brand__tagline">…für Gäste, die gern wiederkommen!</p>
    </div>
  </section>

</main>
</body>
</html>
```